Brisk Pelican Crypto Token Website

Website for a new crypto currency backed up by a hedge fund, 4-5 pages. Needs to have a modern finance, investment, wall street, crypto, tech feel. Looking for the "cool webpage" response. Looking for big pictures and the feel of an Advertisement. Not a lot of white space. Pages will not be content heavy: 1) Brisk Pelican/Investment Case 2) Statistics 3) How to Buy 4) Media/Community
Please create a coin mockup in gold
please work on logo
bring crypto images into the page

Target Market(s)

Investors, News outlets

Industry/Entity Type

Business, Finance, Crypto

Coding

Coded - Design and coding required

Number of Pages Required

5+ page

Font styles to use
Serif

Requirements
Must have
• must catch attention right away, must have serious/ business /modern /tech / cool feel
Nice to have
• Look professional, look like ad (big pictures), animation?
Should not have
• too many colors

```html
<!DOCTYPE html>
<html lang="en">
<head>
<meta charset="utf-8">
<title>Brisk Pelican LLC</title>
<link href="https://fonts.googleapis.com/css2?family=Noto+Serif:ital,wght@0,400;0,700;1,400&family=Arimo:ital,wght@0,400;0,700;1,400&display=swap" rel="stylesheet">
<style>
:root{
  --navy:#0f4f6e;
  --teal:#148a9e;
  --teal-soft:#1f8ea3;
  --grey-bg:#efefef;
  --ink:#2b2b2b;
  --muted:#777;
  --black:#050505;
  --white:#fff;
}
*{margin:0;padding:0;box-sizing:border-box}
html,body{width:1200px;height:3939px;overflow:hidden}
body{position:relative;font-family:"Arimo",Arial,sans-serif;color:var(--ink);background:var(--white)}
.serif{font-family:"Noto Serif",Georgia,serif}
.abs{position:absolute}
section,header,footer{position:absolute;left:0;width:1200px}

/* header */
.site-header{top:0;height:165px;background:var(--navy)}
.brand{left:100px;top:18px;width:250px;text-align:center;color:var(--white);font-family:"Noto Serif",Georgia,serif;font-weight:700}
.brand-mark{width:54px;height:54px;border-radius:50%;background:var(--teal);margin:0 auto 20px}
.brand-name{font-size:16px;letter-spacing:.5px}
.brand-tag{font-size:14px;margin-top:2px}
.call-icon{left:850px;top:20px;width:66px;height:66px;border-radius:50%;background:var(--teal);display:flex;align-items:center;justify-content:center}
.call-text{left:930px;top:40px;color:var(--white);font-family:"Noto Serif",Georgia,serif;font-size:19px}
.main-nav a{position:absolute;top:116px;color:var(--white);font-family:"Noto Serif",Georgia,serif;font-size:15px;text-decoration:none}

/* hero */
.hero{top:165px;height:717px;background:linear-gradient(135deg,#d9dcdc 0%,#a9aeb0 35%,#6d7273 60%,#3b3f42 100%)}
.hero-title{left:396px;top:440px;width:408px;height:66px;background:rgba(31,142,163,.85);color:var(--white);font-size:34px;display:flex;align-items:center;justify-content:center}
.hero-sub{left:209px;top:515px;width:782px;height:65px;background:rgba(18,80,115,.85);color:var(--white);font-size:26px;display:flex;align-items:center;justify-content:center}

/* cta band */
.cta{top:882px;height:187px;background:var(--teal)}
.cta-mascot{left:122px;top:12px;width:176px;height:166px;border-radius:12px;background:linear-gradient(160deg,#3fb3c4,#0f6f82)}
.cta-title{left:318px;top:55px;color:var(--white);font-size:31px}
.cta-sub{left:318px;top:106px;color:var(--white);font-size:14px;font-family:"Noto Serif",Georgia,serif}
.cta-btn{left:864px;top:67px;width:202px;height:57px;border:2px solid var(--white);border-radius:30px;color:var(--white);font-size:18px;display:flex;align-items:center;justify-content:center}

/* section heads */
.sec-title{width:1200px;text-align:center;font-size:40px}
.sec-rule{left:573px;width:54px;height:2px;background:var(--teal)}
.sec-sub{width:1200px;text-align:center;font-size:15px}

/* services */
.services{top:1069px;height:702px;background:var(--grey-bg)}
.card{width:469px;height:193px;background:var(--white);box-shadow:0 2px 8px rgba(0,0,0,.15)}
.card-icon{left:18px;top:24px;width:96px;height:96px;border-radius:50%;background:var(--teal);display:flex;align-items:center;justify-content:center}
.card h3{position:absolute;left:142px;top:22px;font-family:"Noto Serif",Georgia,serif;font-weight:400;font-size:28px;color:#333}
.card p{position:absolute;left:142px;top:72px;width:305px;font-size:13px;line-height:26px;color:var(--muted)}

/* about */
.about{top:1771px;height:587px;background:linear-gradient(90deg,#050303 0%,#120806 45%,#2a140c 70%,#3a1d10 100%)}
.about-photo{left:660px;top:20px;width:400px;height:567px;background:linear-gradient(180deg,#2b2522,#0b0908);border-radius:180px 180px 0 0}
.about h2{position:absolute;left:112px;top:72px;font-size:58px;color:var(--teal);font-weight:400}
.about p{position:absolute;left:112px;top:178px;width:497px;color:#d8d8d8;font-size:13px;line-height:25.8px;text-align:justify}
.about-btn{left:112px;top:440px;width:180px;height:55px;border-radius:30px;background:var(--teal);color:var(--white);font-size:17px;display:flex;align-items:center;justify-content:center}

/* testimonial */
.testimonial{top:2358px;height:407px;background:linear-gradient(90deg,#1b8ea0,#16879b 50%,#128094)}
.avatar{left:539px;top:46px;width:122px;height:122px;border-radius:50%;border:3px solid var(--white);background:linear-gradient(160deg,#b88a6a,#5b3a28)}
.arrow-box{top:183px;width:43px;height:40px;border:1px solid var(--white);display:flex;align-items:center;justify-content:center}
.quote{left:255px;top:182px;width:690px;text-align:center;color:var(--white);font-style:italic;font-size:15px;line-height:28px}
.quote-mark{font-family:"Noto Serif",Georgia,serif;font-weight:700;font-style:normal;font-size:34px;line-height:0;vertical-align:-10px}
.t-name{width:1200px;top:306px;text-align:center;color:var(--white);font-size:17px}
.t-role{width:1200px;top:338px;text-align:center;color:var(--white);font-style:italic;font-size:15px}

/* blog */
.blog{top:2765px;height:709px;background:var(--navy)}
.post{top:183px;width:309px;height:456px;background:var(--white)}
.post-img{left:0;top:0;width:309px;height:234px}
.post-date{left:23px;top:260px;height:26px;padding:0 10px;background:var(--teal);color:var(--white);font-size:12px;display:flex;align-items:center}
.post h4{position:absolute;left:23px;top:303px;width:270px;font-family:"Noto Serif",Georgia,serif;font-weight:400;font-size:17px;line-height:26px;color:#333}
.post p{position:absolute;left:23px;top:366px;width:270px;font-size:13px;line-height:24px;color:var(--muted)}

/* footer */
.site-footer{top:3474px;height:465px;background:var(--black);color:var(--white)}
.foot-nav a{position:absolute;top:36px;color:var(--white);font-family:"Noto Serif",Georgia,serif;font-size:15px;text-decoration:none}
.rule{left:112px;width:976px;height:1px;background:#2a2a2a}
.foot-head{top:120px;font-size:21px}
.field{background:var(--white);color:#333;font-size:11px;padding:10px 12px}
.submit{left:110px;top:324px;width:99px;height:35px;background:var(--teal);color:var(--white);font-size:13px;display:flex;align-items:center;justify-content:center}
.info-icon{width:44px;height:44px;border:2px solid var(--white);border-radius:50%;display:flex;align-items:center;justify-content:center}
.info-label{font-family:"Noto Serif",Georgia,serif;font-size:15px}
.info-value{font-size:13px;margin-top:3px}
.foot-brand{left:840px;top:120px;width:250px;text-align:center;font-family:"Noto Serif",Georgia,serif;font-weight:700}
.social{top:276px;width:36px;height:36px;border:2px solid var(--white);border-radius:50%}
.copyright{top:415px;width:1200px;text-align:center;font-family:"Noto Serif",Georgia,serif;font-size:14px}
</style>
</head>
<body>

<header class="site-header">
  <div class="abs brand">
    <div class="brand-mark"></div>
    <div class="brand-name">BRISK PELICAN LLC</div>
    <div class="brand-tag">"Where Markets Meet Tomorrow"</div>
  </div>
  <div class="abs call-icon">
    <svg width="24" height="24" viewBox="0 0 24 24"><path fill="#fff" d="M6.6 10.8a15.1 15.1 0 0 0 6.6 6.6l2.2-2.2a1 1 0 0 1 1-.25 11.4 11.4 0 0 0 3.6.57 1 1 0 0 1 1 1V20a1 1 0 0 1-1 1A17 17 0 0 1 3 4a1 1 0 0 1 1-1h3.5a1 1 0 0 1 1 1c0 1.25.2 2.45.57 3.57a1 1 0 0 1-.25 1z"/></svg>
  </div>
  <div class="abs call-text">Call : 000.121.1231</div>
  <nav class="main-nav">
    <a style="left:443px">Home</a>
    <a style="left:537px">Brisk Pelican</a>
    <a style="left:696px">Statistics</a>
    <a style="left:813px">How to Buy</a>
    <a style="left:946px">Media/Community</a>
  </nav>
</header>

<section class="hero" role="img" aria-label="Photo of business colleagues shaking hands in a bright modern office">
  <div class="abs hero-title serif">BRISK PELICAN</div>
  <div class="abs hero-sub serif">SED UT PERSPICIATIS UNDE OMNIS ISTE NATUS ERROR</div>
</section>

<section class="cta">
  <div class="abs cta-mascot" role="img" aria-label="Illustration of the cartoon mascot"></div>
  <div class="abs cta-title serif">LET'S WORK TOGETHER</div>
  <div class="abs cta-sub">SED UT PERSPICIATIS UNDE OMNIS ISTE NATUS ERROR VOLUPTATEM</div>
  <div class="abs cta-btn serif">GET STARTED</div>
</section>

<section class="services">
  <div class="abs sec-title serif" style="top:44px">Our <span style="color:var(--teal)">Services</span></div>
  <div class="abs sec-rule" style="top:105px"></div>
  <div class="abs sec-sub" style="top:127px;color:#222">Sed ut perspiciatis unde omnis iste natus error sit voluptatem accusantium doloremque</div>

  <div class="abs card" style="left:112px;top:198px">
    <div class="abs card-icon"><svg width="54" height="54" viewBox="0 0 54 54" fill="none" stroke="#fff" stroke-width="2"><rect x="6" y="12" width="34" height="22" rx="2"/><circle cx="23" cy="23" r="6"/><ellipse cx="40" cy="36" rx="9" ry="3"/><path d="M31 36v10c0 1.7 4 3 9 3s9-1.3 9-3V36M31 41c0 1.7 4 3 9 3s9-1.3 9-3"/></svg></div>
    <h3>Finance</h3>
    <p>Sed ut perspiciatis unde omnis iste natus error sit voluptatem accusantium doloremque laudantium, omnis&nbsp; totam rem aperiam eaque ipsa quae ab illo inventore veritatis et quasi architecto....</p>
  </div>
  <div class="abs card" style="left:618px;top:198px">
    <div class="abs card-icon"><svg width="56" height="56" viewBox="0 0 56 56" fill="none" stroke="#fff" stroke-width="2"><path d="M8 48h42M12 46V34h6v12M22 46V28h6v18M32 46V22h6v24M42 46V14h6v32M12 28l14-10 8 4 14-12"/><text x="8" y="20" fill="#fff" stroke="none" font-size="14" font-family="Arial" font-weight="700">$</text></svg></div>
    <h3>Investment</h3>
    <p>Sed ut perspiciatis unde omnis iste natus error sit voluptatem accusantium doloremque laudantium, omnis&nbsp; totam rem aperiam eaque ipsa quae ab illo inventore veritatis et quasi architecto....</p>
  </div>
  <div class="abs card" style="left:112px;top:422px">
    <div class="abs card-icon"><svg width="52" height="52" viewBox="0 0 52 52" fill="none" stroke="#fff" stroke-width="2.2"><path d="M6 18L26 6l20 12zM8 18h36M12 22v18M20 22v18M32 22v18M40 22v18M6 42h40M4 47h44"/></svg></div>
    <h3>Wall Street</h3>
    <p>Sed ut perspiciatis unde omnis iste natus error sit voluptatem accusantium doloremque laudantium, omnis&nbsp; totam rem aperiam eaque ipsa quae ab illo inventore veritatis et quasi architecto....</p>
  </div>
  <div class="abs card" style="left:618px;top:422px">
    <div class="abs card-icon"><svg width="56" height="56" viewBox="0 0 56 56" fill="none" stroke="#fff" stroke-width="2"><path d="M10 8l8-4 8 4v9l-8 4-8-4zM30 8l8-4 8 4v9l-8 4-8-4zM10 35l8-4 8 4v9l-8 4-8-4zM30 35l8-4 8 4v9l-8 4-8-4zM26 13h4M26 40h4M18 21v10M38 21v10"/></svg></div>
    <h3>Crypto</h3>
    <p>Sed ut perspiciatis unde omnis iste natus error sit voluptatem accusantium doloremque laudantium, omnis&nbsp; totam rem aperiam eaque ipsa quae ab illo inventore veritatis et quasi architecto....</p>
  </div>
</section>

<section class="about">
  <div class="abs about-photo" role="img" aria-label="Photo of a businessman in a dark suit and red tie"></div>
  <h2 class="serif">About Us</h2>
  <p>Sed ut perspiciatis unde omnis iste natus error sit voluptatem accusantium dolo remque laudantium, totam rem aperiam, eaque ipsa quae ab illo inventore veritatis et quasi architecto beatae vitae dicta sunt explicabo. Nemo enim ipsam voluptatem quia voluptas sit aspernatur aut odit aut fugit, sed quia consequuntur magni dolores eos qui ratione voluptatem sequi nesciunt. Neque porro quisquam est, qui dolorem ipsum quia dolor sit amet, consectetur, adipisci velit, sed quia non numquam eius modi tempora incidunt ut labore et dolore magnam aliquam quaerat voluptatem. Ut enim ad minima veniam, quis nostrum exercitationem ullam&nbsp; laboriosam, nisi ut natus error sit&nbsp; aliquid ex ea commodi consequatur</p>
  <div class="abs about-btn serif">LEARN MORE</div>
</section>

<section class="testimonial">
  <div class="abs avatar" role="img" aria-label="Portrait photo of the client"></div>
  <div class="abs arrow-box" style="left:137px"><svg width="10" height="14" viewBox="0 0 10 14"><path d="M8 2L3 7l5 5" stroke="#fff" stroke-width="2" fill="none"/></svg></div>
  <div class="abs arrow-box" style="left:1020px"><svg width="10" height="14" viewBox="0 0 10 14"><path d="M2 2l5 5-5 5" stroke="#fff" stroke-width="2" fill="none"/></svg></div>
  <div class="abs quote"><span class="quote-mark">&ldquo;</span> Sed ut perspiciatis unde omnis iste natus error sit voluptatem accusantium doloremque laudantium, totam rem aperiam, eaque ipsa quae ab illo inventore veritatis et quasi architecto beatae vitae dicta sunt explicabo. Nemo enim ipsam voluptatem quia voluptas sit aspernatur aut odit aut fugit, sed quia consequuntur magni dolores eos qui ratione voluptatem sequi nesciunt. <span class="quote-mark">&rdquo;</span></div>
  <div class="abs t-name serif">-LENA HART</div>
  <div class="abs t-role">Sed ut perspiciatis unde</div>
</section>

<section class="blog">
  <div class="abs sec-title serif" style="top:40px;color:var(--white)">Latest Blog</div>
  <div class="abs sec-rule" style="top:104px;background:var(--white)"></div>
  <div class="abs sec-sub" style="top:126px;color:var(--white)">Sed ut perspiciatis unde omnis iste natus error sit voluptatem accusantium doloremque</div>

  <div class="abs post" style="left:112px">
    <div class="abs post-img" role="img" aria-label="Photo of two analysts reviewing charts at a trading desk" style="background:linear-gradient(135deg,#cfd4d6,#6f7a80 60%,#1e2a30)"></div>
    <div class="abs post-date">20 November 2021</div>
    <h4>Sed ut perspiciatis unde omnis iste natus error sit</h4>
    <p>Nemo enim ipsam voluptatem quia volupta sit aspernatur aut odit aut fugit, sed ration evoluptatem sequi nesciunt.</p>
  </div>
  <div class="abs post" style="left:445px">
    <div class="abs post-img" role="img" aria-label="Photo of a businessman working on a laptop" style="background:linear-gradient(135deg,#e8e8e8,#9aa0a4 50%,#1d2b3c)"></div>
    <div class="abs post-date">20 November 2021</div>
    <h4>Sed ut perspiciatis unde omnis iste natus error sit</h4>
    <p>Nemo enim ipsam voluptatem quia volupta sit aspernatur aut odit aut fugit, sed ration evoluptatem sequi nesciunt.</p>
  </div>
  <div class="abs post" style="left:778px">
    <div class="abs post-img" role="img" aria-label="Photo of a team meeting in a modern office" style="background:linear-gradient(135deg,#3a3d40,#8a8c8d 50%,#c9c6c0)"></div>
    <div class="abs post-date">20 November 2021</div>
    <h4>Sed ut perspiciatis unde omnis iste natus error sit</h4>
    <p>Nemo enim ipsam voluptatem quia volupta sit aspernatur aut odit aut fugit, sed ration evoluptatem sequi nesciunt.</p>
  </div>
</section>

<footer class="site-footer">
  <nav class="foot-nav">
    <a style="left:277px">Home</a>
    <a style="left:370px">Brisk Pelican</a>
    <a style="left:529px">Statistics</a>
    <a style="left:647px">How to Buy</a>
    <a style="left:780px">Media/Community</a>
  </nav>
  <div class="abs rule" style="top:86px"></div>

  <div class="abs foot-head serif" style="left:113px">CONTACT US</div>
  <div class="abs field" style="left:112px;top:173px;width:182px;height:36px">First Name :</div>
  <div class="abs field" style="left:303px;top:173px;width:182px;height:36px">Last Name :</div>
  <div class="abs field" style="left:112px;top:217px;width:182px;height:35px">Email :</div>
  <div class="abs field" style="left:303px;top:217px;width:182px;height:35px">Phone :</div>
  <div class="abs field" style="left:112px;top:260px;width:373px;height:54px">Message :</div>
  <div class="abs submit">SUBMIT</div>

  <div class="abs foot-head serif" style="left:563px">ADDRESS</div>
  <div class="abs info-icon" style="left:553px;top:169px"><svg width="14" height="18" viewBox="0 0 14 18"><path fill="#fff" d="M7 0a7 7 0 0 0-7 7c0 5 7 11 7 11s7-6 7-11a7 7 0 0 0-7-7zm0 9.5A2.5 2.5 0 1 1 7 4.5a2.5 2.5 0 0 1 0 5z"/></svg></div>
  <div class="abs" style="left:612px;top:176px"><div class="info-label">ADDRESS</div><div class="info-value"># 125 Lorem Ipsum Dummy</div></div>
  <div class="abs info-icon" style="left:553px;top:232px"><svg width="16" height="16" viewBox="0 0 24 24"><path fill="#fff" d="M6.6 10.8a15.1 15.1 0 0 0 6.6 6.6l2.2-2.2a1 1 0 0 1 1-.25 11.4 11.4 0 0 0 3.6.57 1 1 0 0 1 1 1V20a1 1 0 0 1-1 1A17 17 0 0 1 3 4a1 1 0 0 1 1-1h3.5a1 1 0 0 1 1 1c0 1.25.2 2.45.57 3.57a1 1 0 0 1-.25 1z"/></svg></div>
  <div class="abs" style="left:612px;top:239px"><div class="info-label">PHONE</div><div class="info-value">000-121-1213</div></div>
  <div class="abs info-icon" style="left:553px;top:297px"><svg width="16" height="12" viewBox="0 0 16 12"><path fill="#fff" d="M0 0h16v12H0zM1.5 1.5L8 6.5l6.5-5z" fill-rule="evenodd"/></svg></div>
  <div class="abs" style="left:612px;top:303px"><div class="info-label">EMAIL</div><div class="info-value">info@companyname.com</div></div>

  <div class="abs foot-brand">
    <div style="width:54px;height:54px;border-radius:50%;background:var(--teal);margin:0 auto 20px"></div>
    <div style="font-size:16px">BRISK PELICAN LLC</div>
    <div style="font-size:14px;margin-top:2px">"Where Markets Meet Tomorrow"</div>
  </div>
  <div class="abs social" style="left:860px"></div>
  <div class="abs social" style="left:902px"></div>
  <div class="abs social" style="left:945px"></div>
  <div class="abs social" style="left:988px"></div>
  <div class="abs social" style="left:1031px"></div>

  <div class="abs rule" style="top:390px"></div>
  <div class="abs copyright">© Copyright 2021 Brisk Pelican.All Rights Reserved</div>
</footer>

</body>
</html>
```